Locksmith Services Tri Fold Flyer

We are a security company that provide all forms of security, we are looking to have tri fold flyers created for each service we offer starting with Locksmith Services, I am looking to work with someone who can design the layout and advise where the text would go where the pictures would go etc as well as tweaking our current logo, I am hoping to find someone that I can work with across all marketing materials for the business.

Our company is called Harbourline Venture Collective , and the Locksmith side will be Harbourline Keysmiths which is why the logo will need tweaking but with the text " Part of the Harbourline Venture Collective "

Logo Text

Our Strap Line is " Protecting People, Property & Assets "

```html
<!DOCTYPE html>
<html lang="en">
<head>
<meta charset="utf-8">
<title>Harbourline Venture Collective – Tri-fold Flyer</title>
<link href="https://fonts.googleapis.com/css2?family=Roboto:ital,wght@0,400;0,500;0,700;0,900;1,400&display=swap" rel="stylesheet">
<style>
  :root{
    --gold:#c9aa6c;
    --gold-light:#d8bd86;
    --ink:#1b1b1b;
    --panel:#232323;
    --panel-mid:#2b2b2b;
    --paper:#ffffff;
    --backdrop:#ececec;
    --text-dark:#1e1e1e;
  }
  *{box-sizing:border-box;margin:0;padding:0}
  html,body{width:1200px;height:3000px;overflow:hidden}
  body{background:var(--backdrop);font-family:'Roboto',Arial,sans-serif;color:var(--paper);position:relative}
  .spread{position:absolute;left:60px;width:1080px;height:768px;display:flex;box-shadow:0 12px 30px rgba(0,0,0,.25);background:var(--ink);overflow:hidden}
  .spread--outside{top:672px}
  .spread--inside{top:1560px}
  .panel{position:relative;width:360px;height:100%;background:linear-gradient(160deg,var(--panel-mid),var(--ink))}
  .panel--mid{background:linear-gradient(160deg,#2f2f2f,#1f1f1f)}
  .copy{font-size:11.5px;line-height:1.38;text-align:justify}
  .copy + .copy{margin-top:16px}
  .gold-box{background:var(--gold);color:var(--text-dark);padding:16px 18px}
  .heading{font-size:18px;font-weight:700;text-transform:uppercase;color:var(--gold)}
  .heading b{color:var(--paper);font-weight:700}
  .photo{position:absolute}
  .rule{position:absolute;height:4px;background:var(--gold)}
  .brand-mark{display:flex;flex-direction:column;align-items:center;gap:8px;text-align:center}
  .brand-mark .dot{width:16px;height:16px;border-radius:50%;background:var(--gold)}
  .brand-mark .name{font-size:15px;font-weight:700;color:var(--gold);line-height:1.2}
  .brand-mark .tag{font-size:10px;font-weight:700;color:var(--gold);line-height:1.3}
  .testimonial{border:1.5px dashed #9a9a9a;border-radius:8px;padding:12px 20px;font-size:10.5px;font-style:italic;line-height:1.4}
  .testimonial .by{text-align:right;margin-top:4px}
  .testimonial .by::before{content:"";display:inline-block;width:70px;border-bottom:1px solid #bbb;margin-right:6px;vertical-align:middle}
  .contact{font-size:11px;line-height:1.6}
  .contact li{list-style:none;display:flex;align-items:center;gap:6px}
  .contact svg{flex:none}
  .services li{list-style:none;display:flex;align-items:center;gap:12px;font-size:12px;margin-bottom:13px}
</style>
</head>
<body>

<!-- Outside spread -->
<section class="spread spread--outside">
  <div class="panel panel--left">
    <div class="gold-box copy" style="position:absolute;left:32px;top:56px;width:296px">Lorem Ipsum is simply dummy text of the printing and typesetting industry. Lorem Ipsum has been the industry's standard dummy text ever since the 1500s, when an unknown printer took a galley of type and scrambled it to make a type specimen book.</div>
    <div style="position:absolute;left:32px;top:236px;width:296px">
      <p class="copy">Lorem Ipsum is simply dummy text of the printing and typesetting industry. Lorem Ipsum has been the industry's standard dummy text ever since the 1500s, when an unknown printer took a galley of type and scrambled it to make a type specimen book.</p>
      <p class="copy">Lorem Ipsum is simply dummy text of the printing and typesetting industry. Lorem Ipsum has been the industry's standard dummy text ever since the 1500s, when an unknown printer took a galley of type and scrambled it to make a type specimen book.</p>
      <p class="copy">Lorem Ipsum is simply dummy text of the printing and typesetting industry. Lorem Ipsum has been the industry's standard dummy text ever since the 1500s, when an unknown printer took a galley of type and scrambled it to make a type specimen book.</p>
    </div>
    <div class="photo" role="img" aria-label="Business handshake over a glowing night city skyline" style="left:0;bottom:0;width:360px;height:200px;background:linear-gradient(135deg,#2b3c5a 0%,#5a7fa8 45%,#1a2638 100%)"></div>
  </div>

  <div class="panel panel--mid">
    <p class="copy" style="position:absolute;left:36px;top:56px;width:290px">Lorem Ipsum is simply dummy text of the printing and typesetting industry. Lorem Ipsum has been the industry's standard dummy text ever since the 1500s, when an unknown printer took a galley of type and scrambled it to make a type specimen book.</p>
    <p style="position:absolute;left:46px;top:198px;font-size:13px;font-weight:700">Protecting People, Property &amp; Assets</p>
    <div class="rule" style="left:0;top:238px;width:360px"></div>
    <h2 class="heading" style="position:absolute;left:0;width:360px;top:268px;text-align:center;font-size:16px">Testimonial</h2>
    <div class="testimonial" style="position:absolute;left:36px;top:304px;width:290px">Lorem Ipsum is simply dummy text of the printing and typesetting industry. Lorem Ipsum has been the industry's standard dummy text ever since the 1500s, when an unknown printer took a galley of type and scrambled it to make a type specimen book.<div class="by">Lorem Ipsum</div></div>
    <div class="testimonial" style="position:absolute;left:36px;top:434px;width:290px">Lorem Ipsum is simply dummy text of the printing and typesetting industry. Lorem Ipsum has been the industry's standard dummy text ever since the 1500s, when an unknown printer took a galley of type and scrambled it to make a type specimen book.<div class="by">Lorem Ipsum</div></div>
    <div class="rule" style="left:0;top:568px;width:360px"></div>
    <div class="brand-mark" style="position:absolute;left:16px;top:608px;width:120px">
      <span class="dot"></span>
      <span class="name" style="font-size:12px">Harbourline Venture Collective</span>
      <span class="tag">Protecting People<br>Property &amp; Assets</span>
    </div>
    <div style="position:absolute;left:160px;top:624px;width:190px">
      <h3 class="heading" style="font-size:15px;padding-bottom:6px;border-bottom:1px solid #777;margin-bottom:10px">Contact <b>Us</b></h3>
      <ul class="contact">
        <li><svg width="11" height="11" viewBox="0 0 24 24"><path fill="#fff" d="M6.6 10.8a15 15 0 006.6 6.6l2.2-2.2c.3-.3.7-.4 1-.2 1.1.4 2.3.6 3.6.6.6 0 1 .4 1 1V20c0 .6-.4 1-1 1A17 17 0 013 4c0-.6.4-1 1-1h3.5c.6 0 1 .4 1 1 0 1.3.2 2.5.6 3.6.1.3 0 .7-.2 1z"/></svg>123 456 7890</li>
        <li style="font-size:9px"><svg width="10" height="10" viewBox="0 0 24 24"><path fill="#fff" d="M2 5h20v14H2z M2 5l10 8 10-8" stroke="#222" stroke-width="1.5"/></svg>hello@harbourlinecollective.com</li>
        <li style="font-size:9px"><svg width="10" height="10" viewBox="0 0 24 24"><circle cx="12" cy="12" r="9" fill="none" stroke="#fff" stroke-width="2.5"/></svg>www.harbourlinecollective.com</li>
      </ul>
    </div>
  </div>

  <div class="panel panel--right">
    <div class="brand-mark" style="position:absolute;left:0;width:360px;top:44px">
      <span class="dot" style="width:22px;height:22px"></span>
      <span class="name" style="font-size:20px">Harbourline<br>Venture Collective</span>
      <span class="tag" style="font-size:11px">Protecting People<br>Property &amp; Assets</span>
    </div>
    <div class="photo" role="img" aria-label="Team stacking hands together in a show of partnership" style="left:0;top:238px;width:360px;height:330px;background:linear-gradient(120deg,#f3e2c6 0%,#d7a57c 45%,#8a6a55 75%,#e9dccb 100%)"></div>
    <div style="position:absolute;left:0;width:360px;top:596px;text-align:center">
      <p style="font-size:36px;font-weight:500;color:var(--gold);line-height:1">HARBOURLINE</p>
      <p style="font-size:21px;font-weight:500;margin-top:6px">VENTURE COLLECTIVE</p>
      <p style="display:inline-block;margin-top:6px;background:var(--gold);color:var(--text-dark);font-size:13px;font-weight:500;padding:3px 12px">Protecting People, Property &amp; Assets</p>
      <p style="font-size:11.5px;font-weight:700;margin-top:18px">www.harbourlinecollective.com</p>
    </div>
  </div>
</section>

<!-- Inside spread -->
<section class="spread spread--inside">
  <div class="panel panel--left">
    <div class="photo" role="img" aria-label="Colleagues standing together by a bright office window" style="left:26px;top:36px;width:308px;height:316px;background:linear-gradient(180deg,#f2efe9 0%,#cfc7bc 55%,#7d7468 100%);border:5px solid var(--gold)"></div>
    <h2 class="heading" style="position:absolute;left:26px;top:396px;font-size:19px">About <b>Us</b></h2>
    <div style="position:absolute;left:26px;top:432px;width:300px">
      <p class="copy">Lorem Ipsum is simply dummy text of the printing and typesetting industry. Lorem Ipsum has been the industry's standard dummy text ever since the 1500s, when an unknown printer took a galley of type and scrambled it to make a type specimen book.</p>
      <p class="copy">Lorem Ipsum is simply dummy text of the printing and typesetting industry. Lorem Ipsum has been the industry's standard dummy text ever since the 1500s, when an unknown printer took a galley of type and scrambled it to make a type specimen book.</p>
      <p class="copy">Lorem Ipsum is simply dummy text of the printing and typesetting industry. Lorem Ipsum has been the industry's standard dummy text ever since the 1500s, when an unknown printer took a galley of type and scrambled it to make a type specimen book.</p>
    </div>
  </div>

  <div class="panel panel--mid">
    <h2 class="heading" style="position:absolute;left:32px;top:52px;font-size:19px">Our <b>Benefits</b></h2>
    <div style="position:absolute;left:32px;top:88px;width:296px">
      <p class="copy">Lorem Ipsum is simply dummy text of the printing and typesetting industry. Lorem Ipsum has been the industry's standard dummy text ever since the 1500s, when an unknown printer took a galley of type and scrambled it to make a type specimen book.</p>
      <p class="copy">Lorem Ipsum is simply dummy text of the printing and typesetting industry. Lorem Ipsum has been the industry's standard dummy text ever since the 1500s, when an unknown printer took a galley of type and scrambled it to make a type specimen book.</p>
      <p class="copy">Lorem Ipsum is simply dummy text of the printing and typesetting industry. Lorem Ipsum has been the industry's standard dummy text ever since the 1500s, when an unknown printer took a galley of type and scrambled it to make a type specimen book.</p>
      <p class="copy">Lorem Ipsum is simply dummy text of the printing and typesetting industry. Lorem Ipsum has been the industry's standard dummy text ever since the 1500s, when an unknown printer took a galley of type and scrambled it to make a type specimen book.</p>
      <p class="copy">Lorem Ipsum is simply dummy text of the printing and typesetting industry. Lorem Ipsum has been the industry's standard dummy text ever since the 1500s, when an unknown printer took a galley of type and scrambled it to make a type specimen book.</p>
    </div>
    <div class="gold-box" style="position:absolute;left:32px;top:648px;width:296px;font-size:20px;font-weight:500;line-height:1.3">Part of the Harbourline Venture Collective</div>
  </div>

  <div class="panel panel--right">
    <div class="gold-box copy" style="position:absolute;left:0;top:0;width:360px;height:146px;padding:40px 30px 0">Lorem Ipsum is simply dummy text of the printing and typesetting industry. Lorem Ipsum has been the industry's standard dummy text ever since the 1500s, when an unknown printer took a galley of type and scrambled it to make a type specimen book.</div>
    <h2 class="heading" style="position:absolute;left:30px;top:176px;font-size:19px">Our <b>Services</b></h2>
    <ul class="services" style="position:absolute;left:30px;top:222px">
      <li><svg width="18" height="18" viewBox="0 0 20 20"><rect x="1" y="1" width="18" height="18" fill="none" stroke="#c9aa6c" stroke-width="2"/><path d="M5 10l4 4 7-8" fill="none" stroke="#c9aa6c" stroke-width="2.5"/></svg>Lorem Ipsum is simply dummy</li>
      <li><svg width="18" height="18" viewBox="0 0 20 20"><rect x="1" y="1" width="18" height="18" fill="none" stroke="#c9aa6c" stroke-width="2"/><path d="M5 10l4 4 7-8" fill="none" stroke="#c9aa6c" stroke-width="2.5"/></svg>Lorem Ipsum is simply dummy</li>
      <li><svg width="18" height="18" viewBox="0 0 20 20"><rect x="1" y="1" width="18" height="18" fill="none" stroke="#c9aa6c" stroke-width="2"/><path d="M5 10l4 4 7-8" fill="none" stroke="#c9aa6c" stroke-width="2.5"/></svg>Lorem Ipsum is simply dummy</li>
      <li><svg width="18" height="18" viewBox="0 0 20 20"><rect x="1" y="1" width="18" height="18" fill="none" stroke="#c9aa6c" stroke-width="2"/><path d="M5 10l4 4 7-8" fill="none" stroke="#c9aa6c" stroke-width="2.5"/></svg>Lorem Ipsum is simply dummy</li>
      <li><svg width="18" height="18" viewBox="0 0 20 20"><rect x="1" y="1" width="18" height="18" fill="none" stroke="#c9aa6c" stroke-width="2"/><path d="M5 10l4 4 7-8" fill="none" stroke="#c9aa6c" stroke-width="2.5"/></svg>Lorem Ipsum is simply dummy</li>
    </ul>
    <div class="photo" role="img" aria-label="Colleagues reviewing documents together in a bright office" style="left:26px;top:416px;width:308px;height:306px;background:linear-gradient(180deg,#f2efe9 0%,#cfc7bc 55%,#7d7468 100%);border:5px solid var(--gold)"></div>
  </div>
</section>

</body>
</html>
```